TA BRAMLEY BUSINESS CARD DESIGN PROJECT

We need to utilize our logo that was expertly created on PixelHarbor and now need to match this with a business card design.

```html
<!DOCTYPE html>
<html lang="en">
<head>
<meta charset="UTF-8">
<title>TA Bramley – Business Card</title>
<link rel="stylesheet" href="https://fonts.googleapis.com/css2?family=Montserrat:wght@400;500;700&display=swap">
<style>
  :root {
    --brand-blue: #0f56aa;
    --ink: #2a2a2a;
    --paper: #ffffff;
    --backdrop: #e9e7e3;
  }
  * { margin: 0; padding: 0; box-sizing: border-box; }
  html, body {
    width: 1200px;
    height: 900px;
    overflow: hidden;
    background: var(--backdrop);
    font-family: 'Montserrat', sans-serif;
  }
  .stage {
    position: relative;
    width: 1200px;
    height: 900px;
  }
  .card {
    position: absolute;
    left: 310px;
    width: 582px;
    height: 332px;
    border-radius: 28px;
    overflow: hidden;
  }
  .card-front { top: 86px; background: var(--paper); }
  .card-back  { top: 470px; background: var(--brand-blue); }

  .identity {
    position: absolute;
    right: 319px;
    top: 138px;
    text-align: right;
  }
  .identity-name {
    color: var(--brand-blue);
    font-weight: 700;
    font-size: 21px;
    letter-spacing: 0.2px;
    line-height: 1.1;
  }
  .identity-title {
    color: var(--ink);
    font-weight: 400;
    font-size: 15px;
    margin-top: 3px;
  }
  .divider {
    position: absolute;
    left: 282px;
    top: 139px;
    width: 2px;
    height: 54px;
    background: var(--brand-blue);
  }
  .contact-list {
    position: absolute;
    left: 301px;
    top: 134px;
    list-style: none;
  }
  .contact-item {
    display: flex;
    align-items: center;
    gap: 6px;
    height: 20px;
    color: var(--ink);
    font-size: 15.5px;
  }
  .contact-icon { width: 12px; height: 12px; fill: var(--brand-blue); flex: none; }
  .address-band {
    position: absolute;
    left: 0;
    top: 285px;
    width: 100%;
    height: 20px;
    background: var(--brand-blue);
    color: var(--paper);
    font-size: 14.5px;
    text-align: center;
    line-height: 20px;
  }
  .brand-name {
    position: absolute;
    inset: 0;
    display: flex;
    align-items: center;
    justify-content: center;
    color: var(--paper);
    font-weight: 700;
    font-size: 50px;
    letter-spacing: 8px;
  }
</style>
</head>
<body>
<main class="stage">
  <section class="card card-front" aria-label="Business card front">
    <div class="identity">
      <p class="identity-name">MARCUS HALE</p>
      <p class="identity-title">Managing Director</p>
    </div>
    <div class="divider"></div>
    <ul class="contact-list">
      <li class="contact-item">
        <svg class="contact-icon" viewBox="0 0 12 12" aria-hidden="true"><path d="M1 4.5C1 2.5 3 2 6 2s5 .5 5 2.5v.8H8.5V4.3H3.5v1H1z"/><path d="M2.5 6h7l1 4.5h-9z"/></svg>
        <span>123 456 789</span>
      </li>
      <li class="contact-item">
        <svg class="contact-icon" viewBox="0 0 12 12" aria-hidden="true"><path d="M1 3h10v.8L6 7 1 3.8z"/><path d="M1 5l5 3.2L11 5v4.5H1z"/></svg>
        <span>info@yourgmail.com</span>
      </li>
      <li class="contact-item">
        <svg class="contact-icon" viewBox="0 0 12 12" aria-hidden="true"><circle cx="6" cy="6" r="5.2"/><path d="M3 3.5l2 1-1 2 1.5 1.5-.5 2M7.5 2l.5 2 2 .5M8 7l1.5 1" stroke="#fff" stroke-width="0.9" fill="none"/></svg>
        <span>www.yourwebsite.com</span>
      </li>
    </ul>
    <div class="address-band">Your address, City State, Zip 1234</div>
  </section>

  <section class="card card-back" aria-label="Business card back">
    <p class="brand-name">TA BRAMLEY</p>
  </section>
</main>
</body>
</html>
```